Brekwell Automotive needs a catchy banner design

We need a design for a banner to be displayed on the fence in the outfield of a baseball stadium to show off our company and have people interested in what we do. We need something catchy that's going to attract people to look over at our banner.
We are a
Complete Automotive Service Company
Tires - Service - Repair - Diesel
We are in a Town called Maple Ridge
(555)314-2609 we would like the phone number to be a descent size so when you are in the stands you can read it.
I have attached what we came up with but like I said we need it to pop more and make the viewer that's looking at it want to look us up.
The Banner size is 24ft long and 10ft tall

```html
<!DOCTYPE html>
<html lang="en">
<head>
<meta charset="utf-8">
<title>Brekwell Automotive – Outfield Banner</title>
<link rel="stylesheet" href="https://fonts.googleapis.com/css2?family=Saira+Semi+Condensed:wght@800&family=Roboto+Condensed:wght@700&display=swap">
<style>
  :root {
    --bg-dark: #1b1c20;
    --bg-mid: #2a2b30;
    --white: #ffffff;
    --blue: #1f5fd9;
    --blue-bright: #2f7bf0;
    --blue-deep: #123f9e;
    --phone-blue: #3274e6;
    --photo-sky: #5b86d8;
    --photo-wall: #5d6066;
    --photo-rock: #8a7a66;
  }
  * { margin: 0; padding: 0; box-sizing: border-box; }
  html, body { width: 1200px; height: 500px; overflow: hidden; background: var(--bg-dark); }
  .banner {
    position: relative;
    width: 1200px; height: 500px;
    overflow: hidden;
    font-family: "Roboto Condensed", "Arial Narrow", sans-serif;
    font-weight: 700;
    color: var(--white);
  }
  .backdrop {
    position: absolute; inset: 0;
    background: radial-gradient(ellipse at 65% 45%, var(--bg-mid) 0%, var(--bg-dark) 70%);
  }
  .hero-photo { position: absolute; left: 0; top: 0; }
  .brand-name {
    position: absolute; left: 990px; top: 60px; width: 134px;
    text-align: center;
    font-family: "Saira Semi Condensed", "Arial Narrow", sans-serif;
    font-weight: 800; font-size: 28px; line-height: 32px; letter-spacing: 1px;
    color: var(--blue-bright);
  }
  .headline {
    position: absolute; left: 498px; top: 88px;
    font-family: "Saira Semi Condensed", "Arial Narrow", sans-serif;
    font-weight: 800; font-size: 36px; line-height: 44px;
    text-transform: uppercase; letter-spacing: 0.5px;
    white-space: nowrap;
  }
  .divider { position: absolute; left: 498px; top: 188px; }
  .divider .accent { position: absolute; left: 0; top: 0; width: 91px; height: 4px; background: var(--blue); }
  .divider .rule { position: absolute; left: 91px; top: 1px; width: 74px; height: 2px; background: var(--white); }
  .services { position: absolute; left: 499px; top: 233px; width: 640px; height: 72px; }
  .service { position: absolute; top: 0; height: 72px; display: flex; align-items: center; }
  .service .label { font-size: 21px; font-weight: 700; margin-left: 15px; letter-spacing: 0.3px; }
  .town {
    position: absolute; left: 498px; top: 333px;
    font-size: 25px; font-weight: 700; letter-spacing: 0.2px; text-transform: uppercase;
    white-space: nowrap;
  }
  .contact { position: absolute; left: 499px; top: 386px; display: flex; align-items: center; }
  .contact .lines { margin-left: 20px; }
  .contact .call { font-size: 14px; font-weight: 700; line-height: 17px; }
  .contact .number { font-size: 25px; font-weight: 700; line-height: 30px; color: var(--phone-blue); letter-spacing: 0.3px; }
</style>
</head>
<body>
<div class="banner">
  <div class="backdrop" role="img" aria-label="Dark, dimmed photo of oil being poured into an engine bay"></div>

  <svg class="hero-photo" width="1200" height="500" viewBox="0 0 1200 500">
    <defs>
      <linearGradient id="photoFill" x1="0" y1="0" x2="0" y2="1">
        <stop offset="0" stop-color="var(--photo-sky)"/>
        <stop offset="0.45" stop-color="var(--photo-wall)"/>
        <stop offset="1" stop-color="var(--photo-rock)"/>
      </linearGradient>
    </defs>
    <polygon points="253,47 430,150 430,350 253,453 77,350 77,150" fill="var(--white)"/>
    <polygon points="253,55 423,154 423,346 253,445 84,346 84,154" fill="url(#photoFill)" role="img" aria-label="Photo of a lifted red pickup truck on rocks outside the shop building"/>
  </svg>

  <div class="brand-name">BREKWELL</div>

  <h1 class="headline">Brekwell Complete<br>Automotive Service Company</h1>

  <div class="divider"><span class="accent"></span><span class="rule"></span></div>

  <svg width="0" height="0" style="position:absolute">
    <defs>
      <linearGradient id="hexBlue" x1="0" y1="0" x2="1" y2="1">
        <stop offset="0" stop-color="var(--blue-bright)"/>
        <stop offset="1" stop-color="var(--blue-deep)"/>
      </linearGradient>
    </defs>
  </svg>

  <div class="services">
    <div class="service" style="left:0">
      <svg width="62" height="72" viewBox="0 0 62 72">
        <polygon points="31,1 61,18.5 61,53.5 31,71 1,53.5 1,18.5" fill="url(#hexBlue)" stroke="var(--blue-bright)" stroke-width="2"/>
        <circle cx="31" cy="36" r="15" fill="none" stroke="var(--white)" stroke-width="3.5"/>
        <circle cx="31" cy="36" r="9" fill="none" stroke="var(--white)" stroke-width="2"/>
        <circle cx="31" cy="36" r="3" fill="var(--white)"/>
        <g stroke="var(--white)" stroke-width="2">
          <line x1="31" y1="27" x2="31" y2="45"/><line x1="22" y1="36" x2="40" y2="36"/>
        </g>
      </svg>
      <span class="label">TIRES</span>
    </div>
    <div class="service" style="left:155px">
      <svg width="62" height="72" viewBox="0 0 62 72">
        <polygon points="31,1 61,18.5 61,53.5 31,71 1,53.5 1,18.5" fill="url(#hexBlue)" stroke="var(--blue-bright)" stroke-width="2"/>
        <circle cx="31" cy="36" r="15" fill="none" stroke="var(--white)" stroke-width="6" stroke-dasharray="6 5.8"/>
        <circle cx="31" cy="36" r="11" fill="var(--white)"/>
        <circle cx="31" cy="36" r="6" fill="var(--blue)"/>
        <line x1="31" y1="36" x2="38" y2="43" stroke="var(--blue)" stroke-width="3"/>
      </svg>
      <span class="label">SERVICE</span>
    </div>
    <div class="service" style="left:326px">
      <svg width="62" height="72" viewBox="0 0 62 72">
        <polygon points="31,1 61,18.5 61,53.5 31,71 1,53.5 1,18.5" fill="url(#hexBlue)" stroke="var(--blue-bright)" stroke-width="2"/>
        <g stroke="var(--white)" stroke-width="4" stroke-linecap="round">
          <line x1="19" y1="24" x2="43" y2="48"/><line x1="43" y1="24" x2="19" y2="48"/>
        </g>
        <circle cx="19" cy="24" r="5" fill="none" stroke="var(--white)" stroke-width="3"/>
        <circle cx="43" cy="48" r="5" fill="none" stroke="var(--white)" stroke-width="3"/>
      </svg>
      <span class="label">REPAIR</span>
    </div>
    <div class="service" style="left:493px">
      <svg width="62" height="72" viewBox="0 0 62 72">
        <polygon points="31,1 61,18.5 61,53.5 31,71 1,53.5 1,18.5" fill="url(#hexBlue)" stroke="var(--blue-bright)" stroke-width="2"/>
        <path d="M20,26 h16 l5,5 v18 h-21 z" fill="none" stroke="var(--white)" stroke-width="3.5" stroke-linejoin="round"/>
        <rect x="25" y="36" width="11" height="8" fill="none" stroke="var(--white)" stroke-width="2"/>
        <line x1="38" y1="26" x2="43" y2="21" stroke="var(--white)" stroke-width="3"/>
        <circle cx="46" cy="28" r="2" fill="var(--white)"/>
      </svg>
      <span class="label">DIESEL</span>
    </div>
  </div>

  <p class="town">We are in a town called Maple Ridge</p>

  <div class="contact">
    <svg width="42" height="48" viewBox="0 0 42 48">
      <polygon points="21,0 42,12 42,36 21,48 0,36 0,12" fill="var(--white)"/>
      <path d="M14,16 c2,-2 4,-1 5,1 l1,3 c0,1 -1,2 -2,3 c1,3 3,5 6,6 c1,-1 2,-2 3,-2 l3,1 c2,1 3,3 1,5 c-2,2 -5,2 -8,0 c-4,-2 -8,-6 -10,-10 c-1,-3 -1,-5 1,-7 z" fill="var(--phone-blue)"/>
    </svg>
    <div class="lines">
      <div class="call">CALL US:</div>
      <div class="number">(555)314-2609</div>
    </div>
  </div>
</div>
</body>
</html>
```